4747 5858

Web(re)design of an existing directory search site www.le5858.be (in Dutch www.de4747.be and in English www.3838.be).

This site is a directory site, i.e. a "white pages" site whereby people can search the phone & details of another person based on a combination of name + city (for instance smith in Brussels); one can also search a company also based on a combination of name + city (for instance Vornak in Brussels); last but not least one can also search the name of the subscriber behind a specific telephone number (also called reverse search).

This site is quite outdated and needs a redesign, see instructions.

We need the output in XD format.

```html
<!DOCTYPE html>
<html lang="en">
<head>
<meta charset="utf-8">
<title>Le 5858 – Directory Search</title>
<link href="https://fonts.googleapis.com/css2?family=Rajdhani:wght@500;600;700&family=Poppins:wght@400&display=swap" rel="stylesheet">
<style>
:root{
  --red:#e3241b;
  --ink:#333333;
  --text:#555555;
  --muted:#6b6b6b;
  --light:#f5f5f5;
  --dark:#232323;
  --white:#ffffff;
}
*{margin:0;padding:0;box-sizing:border-box}
html,body{width:1200px;height:2955px;overflow:hidden}
body{font-family:'Rajdhani',sans-serif;color:var(--ink);background:var(--white);position:relative}
.abs{position:absolute}

/* header */
.site-header{position:absolute;left:0;top:0;width:1200px;height:117px;background:var(--white)}
.brand{position:absolute;left:110px;top:30px;display:flex;align-items:center;gap:10px;font-weight:700;font-size:44px;color:var(--red);line-height:1}
.brand-dot{width:16px;height:16px;border-radius:50%;background:var(--red)}
.btn-start{position:absolute;left:945px;top:15px;width:145px;height:47px;border-radius:24px;background:var(--red);color:var(--white);font-weight:600;font-size:17px;display:flex;align-items:center;justify-content:center}
.main-nav{position:absolute;top:76px;left:0;width:1200px;font-weight:600;font-size:17px;color:#444}
.main-nav span{position:absolute}
.main-nav .active{color:var(--red)}

/* hero */
.hero{position:absolute;left:0;top:117px;width:1200px;height:672px;background:linear-gradient(135deg,#4a3a30 0%,#6b5648 35%,#8a7464 50%,#3e3530 75%,#2a2622 100%)}
.hero-shade{position:absolute;inset:0;background:rgba(0,0,0,.28)}
.hero-title{position:absolute;left:0;width:1200px;top:322px;text-align:center;color:var(--white);font-weight:700;font-size:84px;line-height:1}
.hero-sub{position:absolute;left:0;width:1200px;top:418px;text-align:center;color:var(--white);font-weight:600;font-size:25px}
.search-bar{position:absolute;left:162px;top:481px;width:877px;height:58px;background:var(--white);border-radius:4px;display:flex;overflow:hidden}
.search-field{flex:0 0 235px;display:flex;align-items:center;padding-left:18px;font-weight:600;font-size:17px;color:#444;position:relative}
.search-field+.search-field::before{content:"";position:absolute;left:0;top:18px;height:22px;border-left:1px solid #999}
.search-field.loc{flex:0 0 298px;justify-content:space-between;padding-right:16px}
.search-btn{flex:1;background:var(--red);color:var(--white);font-weight:700;font-size:18px;display:flex;align-items:center;justify-content:center}

/* welcome */
.section-title{position:absolute;left:0;width:1200px;text-align:center;font-weight:600;font-size:38px;color:var(--ink);line-height:1}
.section-title em{font-style:normal;color:var(--red)}
.intro{position:absolute;left:0;width:1200px;text-align:center;font-weight:500;font-size:16px;line-height:28px;color:var(--text)}
.service{position:absolute;width:260px;text-align:center}
.service-icon{width:130px;height:130px;border:2px solid var(--red);border-radius:50%;margin:0 auto;display:flex;align-items:center;justify-content:center}
.service h3{font-weight:600;font-size:20px;margin-top:18px;color:var(--ink)}
.service p{font-weight:500;font-size:14px;line-height:26px;color:var(--text);margin-top:10px}

/* professional */
.pro{position:absolute;left:0;top:1333px;width:1200px;height:985px;background:var(--light)}
.rule{position:absolute;height:2px;background:var(--red)}
.pro-heading{position:absolute;font-weight:600;font-size:28px;color:var(--ink)}
.pro-text{position:absolute;width:476px;font-family:'Poppins',sans-serif;font-size:13.5px;line-height:26px;color:var(--muted);text-align:justify}
.btn-outline{position:absolute;width:147px;height:53px;border:1px solid var(--red);border-radius:27px;color:var(--red);font-weight:600;font-size:18px;display:flex;align-items:center;justify-content:center}
.illustration{position:absolute;border-radius:6px}

/* newsletter */
.newsletter{position:absolute;left:0;top:2318px;width:1200px;height:305px;background:var(--red);color:var(--white)}
.newsletter h2{position:absolute;left:0;width:1200px;top:48px;text-align:center;font-weight:600;font-size:38px}
.newsletter p{position:absolute;left:0;width:1200px;top:104px;text-align:center;font-weight:500;font-size:16px;line-height:28px}
.signup{position:absolute;left:231px;top:179px;width:739px;height:58px;border-radius:29px;background:var(--white);overflow:hidden;display:flex}
.signup-input{flex:1;display:flex;align-items:center;padding-left:26px;font-weight:500;font-size:16px;color:#555}
.signup-btn{flex:0 0 138px;background:var(--dark);display:flex;align-items:center;justify-content:center;font-weight:700;font-size:18px;color:var(--white)}

/* footer */
.site-footer{position:absolute;left:0;top:2623px;width:1200px;height:332px;background:var(--dark);color:var(--white)}
.footer-brand{position:absolute;left:0;width:1200px;top:52px;display:flex;justify-content:center;align-items:center;gap:12px;font-weight:700;font-size:52px;color:var(--red);line-height:1}
.footer-nav{position:absolute;left:0;width:1200px;top:162px;display:flex;justify-content:center;gap:47px;font-weight:600;font-size:18px}
.social{position:absolute;left:0;width:1200px;top:217px;display:flex;justify-content:center;gap:7px}
.social span{width:36px;height:36px;border:1.5px solid var(--white);border-radius:50%}
.copyright{position:absolute;left:0;width:1200px;top:280px;text-align:center;font-weight:500;font-size:15px}
</style>
</head>
<body>

<header class="site-header">
  <div class="brand"><span class="brand-dot"></span>5858</div>
  <div class="btn-start">Get Started</div>
  <nav class="main-nav">
    <span class="active" style="left:505px">Home</span>
    <span style="left:592px">Individuals</span>
    <span style="left:715px">Companies</span>
    <span style="left:840px">Inversed annual</span>
    <span style="left:998px">International</span>
  </nav>
</header>

<section class="hero">
  <div class="abs" style="inset:0" role="img" aria-label="Photo of a woman with a laptop sitting on a bench in a city street"></div>
  <div class="hero-shade"></div>
  <h1 class="hero-title">Le 5858</h1>
  <p class="hero-sub">Sed ut perspiciatis unde omnis iste natus error sit voluptatem</p>
  <div class="search-bar">
    <div class="search-field">Surname :</div>
    <div class="search-field">First name :</div>
    <div class="search-field loc">Locality :
      <svg width="12" height="16" viewBox="0 0 12 16"><path d="M6 0a6 6 0 0 0-6 6c0 4.5 6 10 6 10s6-5.5 6-10a6 6 0 0 0-6-6zm0 8.2A2.2 2.2 0 1 1 6 3.8a2.2 2.2 0 0 1 0 4.4z" fill="#444"/></svg>
    </div>
    <div class="search-btn">SEARCH</div>
  </div>
</section>

<section class="welcome">
  <h2 class="section-title" style="top:847px">Welcome to <em>Le5858</em></h2>
  <p class="intro" style="top:900px">Sed ut perspiciatis unde omnis iste natus error sit voluptatem accusantium doloremque laudantium, totam<br>aperiam, eaque ipsa quae ab illo inventore veritatis et quasi</p>

  <div class="service" style="left:137px;top:1014px">
    <div class="service-icon">
      <svg width="60" height="60" viewBox="0 0 60 60" fill="none" stroke="#333" stroke-width="2"><circle cx="30" cy="18" r="9"/><path d="M12 54c0-11 8-19 18-19s18 8 18 19"/></svg>
    </div>
    <h3>Find a Person</h3>
    <p>Sed ut perspiciatis unde omnis iste natus error sit voluptatem accusantium dolorem que laudantium, totam</p>
  </div>
  <div class="service" style="left:469px;top:1014px">
    <div class="service-icon">
      <svg width="60" height="60" viewBox="0 0 60 60" fill="none" stroke="#333" stroke-width="2"><path d="M14 8l8 0 4 11-5 4c3 7 8 12 15 15l4-5 11 4v8c0 3-2 5-5 5C26 50 10 34 10 12c0-3 2-4 4-4z"/><path d="M36 10a14 14 0 0 1 14 14M36 3a21 21 0 0 1 21 21"/></svg>
    </div>
    <h3>Look Up a Phone Number</h3>
    <p>Sed ut perspiciatis unde omnis iste natus error sit voluptatem accusantium dolorem que laudantium, totam</p>
  </div>
  <div class="service" style="left:802px;top:1014px">
    <div class="service-icon">
      <svg width="60" height="60" viewBox="0 0 60 60" fill="none" stroke="#333" stroke-width="2"><circle cx="24" cy="24" r="15"/><path d="M35 35l16 16"/></svg>
    </div>
    <h3>Screen a Tenant</h3>
    <p>Sed ut perspiciatis unde omnis iste natus error sit voluptatem accusantium dolorem que laudantium, totam</p>
  </div>
</section>

<section class="pro">
  <h2 class="section-title" style="top:52px">Are you a <em>professional?</em></h2>
  <div class="rule" style="left:582px;top:101px;width:36px"></div>

  <h3 class="pro-heading" style="left:143px;top:197px">Sed ut perspiciatis unde omnis iste</h3>
  <div class="rule" style="left:143px;top:249px;width:55px"></div>
  <p class="pro-text" style="left:144px;top:277px">Sed ut perspiciatis unde omnis iste natus error sit voluptatem accusantium doloremque laudantium, totam rem aperiam, eaque ipsa quae ab illo inventore veritatis et quasi architecto beatae vitae dicta sunt explicabo. Nemo enim ipsam voluptatem quia voluptas sit aspernatur aut odit aut fugit, sed quia conse quuntur magni dolores eos qui ratione voluptatem sequi nesciunt.</p>
  <div class="btn-outline" style="left:147px;top:435px">Read More</div>
  <div class="illustration" style="left:680px;top:137px;width:360px;height:390px;background:linear-gradient(180deg,#eeeae4 0%,#f0d9cf 55%,#e8dccb 100%)" role="img" aria-label="Illustration of a woman working on a laptop at a desk with a wall clock and binders"></div>

  <div class="illustration" style="left:125px;top:572px;width:380px;height:367px;background:linear-gradient(180deg,#ececec 0%,#f2dcd2 55%,#e6dacb 100%)" role="img" aria-label="Illustration of a woman at a desk with a lamp, shelves and a sleeping cat"></div>
  <h3 class="pro-heading" style="left:554px;top:626px">Sed ut perspiciatis unde omnis iste</h3>
  <div class="rule" style="left:554px;top:678px;width:55px"></div>
  <p class="pro-text" style="left:556px;top:706px">Sed ut perspiciatis unde omnis iste natus error sit voluptatem accusantium doloremque laudantium, totam rem aperiam, eaque ipsa quae ab illo inventore veritatis et quasi architecto beatae vitae dicta sunt explicabo. Nemo enim ipsam voluptatem quia voluptas sit aspernatur aut odit aut fugit, sed quia conse quuntur magni dolores eos qui ratione voluptatem sequi nesciunt.</p>
  <div class="btn-outline" style="left:558px;top:864px">Read More</div>
</section>

<section class="newsletter">
  <h2>Our Newsletter Signup</h2>
  <p>Sed ut perspiciatis unde omnis iste natus error sit voluptatem accusantium doloremque laudantium, totam<br>aperiam, eaque ipsa quae ab illo inventore veritatis et quasi</p>
  <div class="signup">
    <div class="signup-input">Enter Your Email:</div>
    <div class="signup-btn">SIGNUP</div>
  </div>
</section>

<footer class="site-footer">
  <div class="footer-brand"><span class="brand-dot"></span>5858</div>
  <nav class="footer-nav">
    <span>Home</span><span>Individuals</span><span>Companies</span><span>Inversed annual</span><span>International</span>
  </nav>
  <div class="social"><span></span><span></span><span></span><span></span><span></span></div>
  <p class="copyright">© 2022 Le5858.All Rights Reserved</p>
</footer>

</body>
</html>
```